A ebook cover to reinvent the imagery of vegetable companion gardening

We needs a ebook design with illustrates minimal as well as clear and concise relevance to vegetable companion gardening . we will add a mock up design and other existing designs to help you gauge and create the sort of illustration fit for our aims.
Book Title: Orchard and Greens 202 – Garden Partner Sowing
Subtitle: Partner Handbook On Raising Crops Through Basic, Natural & Lasting Plot Methods
(Perfect For Beginners)
Author: Amber Hollow
Size: 5.5 x 8.5

```html
<!DOCTYPE html>
<html lang="en">
<head>
<meta charset="utf-8">
<title>Orchard and Greens 202 – Garden Partner Sowing</title>
<link href="https://fonts.googleapis.com/css2?family=Oswald:wght@700&family=Archivo:wght@800&family=Maven+Pro:wght@700&family=Yellowtail&display=swap" rel="stylesheet">
<style>
  :root {
    --backdrop: #2e2e2e;
    --paper: #ffffff;
    --sun-band: #fde39a;
    --leaf-band: #c6e2a0;
    --leaf: #8cc63f;
    --berry: #d6175c;
    --produce-a: #e8b23a;
    --produce-b: #d9412f;
    --produce-c: #9cc94a;
  }
  * { margin: 0; padding: 0; box-sizing: border-box; }
  html, body {
    width: 960px; height: 1200px; overflow: hidden;
    background: var(--backdrop);
  }
  .cover-frame {
    position: absolute; left: 117px; top: 40px;
    width: 725px; height: 1120px;
    overflow: hidden;
  }
  .cover {
    position: absolute; left: 0; top: 0;
    width: 872px; height: 1346px;
    transform: scale(0.8316);
    transform-origin: 0 0;
    background: var(--paper);
  }
  .cover-art { position: absolute; inset: 0; }
  .title {
    position: absolute; right: 71px; top: 78px;
    text-align: right;
    font-family: "Oswald", sans-serif; font-weight: 700;
    font-size: 104px; line-height: 112px;
    letter-spacing: 1px;
  }
  .title-line-1 { color: var(--leaf); display: block; }
  .title-line-2 { color: var(--berry); display: block; }
  .series-line {
    position: absolute; right: 79px; top: 316px;
    font-family: "Archivo", sans-serif; font-weight: 800;
    font-size: 26px; color: var(--berry); letter-spacing: 0.5px;
  }
  .subtitle {
    position: absolute; left: 0; width: 872px; top: 1046px;
    text-align: center;
    font-family: "Maven Pro", sans-serif; font-weight: 700;
    font-size: 21.5px; line-height: 30px; color: var(--berry);
  }
  .audience {
    position: absolute; left: 0; width: 872px; top: 1128px;
    text-align: center;
    font-family: "Yellowtail", cursive;
    font-size: 44px; color: var(--leaf);
  }
  .rule {
    position: absolute; left: 123px; width: 626px; top: 1220px;
    height: 6px; background: var(--leaf);
  }
  .author {
    position: absolute; left: 0; width: 872px; top: 1248px;
    text-align: center;
    font-family: "Maven Pro", sans-serif; font-weight: 700;
    font-size: 37px; color: var(--berry); letter-spacing: 0.5px;
  }
</style>
</head>
<body>
  <div class="cover-frame">
    <div class="cover">
      <svg class="cover-art" viewBox="0 0 872 1346" width="872" height="1346">
        <defs>
          <linearGradient id="produce-tones" x1="0" y1="0" x2="1" y2="1">
            <stop offset="0" stop-color="var(--produce-a)"/>
            <stop offset="0.5" stop-color="var(--produce-b)"/>
            <stop offset="1" stop-color="var(--produce-c)"/>
          </linearGradient>
        </defs>
        <polygon class="band-sun" points="0,0 279,0 0,1290" fill="var(--sun-band)"/>
        <polygon class="band-leaf" points="872,53 872,1346 593,1346" fill="var(--leaf-band)"/>
        <polygon class="produce-photo" role="img"
          aria-label="Photograph of a pile of fresh fruit: bananas, kiwi, grapes, grapefruit, apples, pear, strawberries, raspberries and blueberries"
          points="0,456 731,456 656,908 0,908" fill="url(#produce-tones)"/>
      </svg>

      <h1 class="title">
        <span class="title-line-1">ORCHARD AND</span>
        <span class="title-line-2">GREENS 202</span>
      </h1>
      <p class="series-line">GARDEN PARTNER SOWING</p>

      <p class="subtitle">Partner Handbook On Raising Crops Through Basic,<br>Natural &amp; Lasting Plot Methods</p>
      <p class="audience">[Perfect For Beginners]</p>
      <div class="rule"></div>
      <p class="author">Author: Amber Hollow</p>
    </div>
  </div>
</body>
</html>
```